Brintel Works - Fast, Efficient and Gas Mainteance for Domestic, Commercial and Industrial clients

We are in the process of purchasing a new business and would like to get a new logo and business card.
Business is a gas maintenance business that also does new gas installations.
Has been established since 1988.
Services include:
Install all types of gas appliances & equipment inc. hot water units
Maintain / repair / replace all types of gas appliances & equipment

Target Market(s)

Domestic, Commercial and Industrial clients

Industry/Entity Type

Business

Contact Information for Business Card

admin@brintelworks.com.au
07 3918 4726
Brintel Works PTY LTD

Logo Text

Gas Fitting & Plumbing Maintenance Specialists

Font styles to use
Sans Serif

Requirements
Must have
• Logo
• Business name, contact number, email address, web address
• Domestic | Commercial | Industrial Est Since 1988
Nice to have
• Possibly a black card with a flame logo to one side
Should not have
• Spelling errors

```html
<!DOCTYPE html>
<html lang="en">
<head>
<meta charset="utf-8">
<title>Brintel Works – Business Card</title>
<link rel="stylesheet" href="https://fonts.googleapis.com/css2?family=Open+Sans:wght@400;700&family=Arimo&family=Great+Vibes&display=swap">
<style>
  :root {
    --page: #d6d6d6;
    --card: #ebebeb;
    --brand-red: #e2543a;
    --ink-grey: #4a4f57;
    --soft-grey: #5c6068;
    --band-blue: #0a6fbe;
    --night: #000000;
    --icon-orange: #f0502d;
    --white: #ffffff;
  }
  * { margin: 0; padding: 0; box-sizing: border-box; }
  html, body { width: 1189px; height: 1200px; overflow: hidden; }
  body { background: var(--page); position: relative; font-family: "Open Sans", sans-serif; }

  .card {
    position: absolute;
    left: 140px;
    width: 917px;
    height: 523px;
    background: var(--card);
    overflow: hidden;
    box-shadow: 0 2px 6px rgba(0,0,0,.18);
  }
  .card--front { top: 46px; }
  .card--back { top: 623px; }

  .brand { position: absolute; white-space: nowrap; }
  .brand__name {
    font-family: "Open Sans", sans-serif;
    font-weight: 700;
    color: var(--brand-red);
    letter-spacing: 0.5px;
    line-height: 1;
    display: flex;
    align-items: baseline;
  }
  .brand__suffix { font-weight: 700; color: var(--ink-grey); margin-left: 14px; }
  .brand__tagline { font-weight: 700; color: var(--ink-grey); line-height: 1; }
  .brand__sectors { color: var(--soft-grey); line-height: 1; display: flex; align-items: baseline; }
  .brand__since { font-family: "Great Vibes", cursive; color: var(--soft-grey); margin-left: 16px; }

  .card--front .brand { left: 261px; top: 70px; }
  .card--front .brand__name { font-size: 40px; }
  .card--front .brand__suffix { font-size: 12px; }
  .card--front .brand__tagline { font-size: 27px; margin-top: 14px; }
  .card--front .brand__sectors { font-size: 15px; margin-top: 14px; }
  .card--front .brand__since { font-size: 26px; }

  .card--back .brand { left: 129px; top: 206px; }
  .card--back .brand__name { font-size: 33px; }
  .card--back .brand__suffix { font-size: 10px; margin-left: 10px; }
  .card--back .brand__tagline { font-size: 22px; margin-top: 11px; }
  .card--back .brand__sectors { font-size: 12.5px; margin-top: 11px; }
  .card--back .brand__since { font-size: 22px; margin-left: 12px; }

  .band-blue { position: absolute; left: 0; top: 257px; width: 100%; height: 22px; background: var(--band-blue); }
  .panel-dark { position: absolute; left: 0; top: 279px; width: 100%; height: 244px; background: var(--night); }

  .contact-list { position: absolute; left: 47px; top: 334px; list-style: none; }
  .contact-list li {
    display: flex; align-items: center;
    height: 29.5px;
    font-family: "Arimo", sans-serif;
    font-size: 26px;
    color: var(--white);
  }
  .contact-icon {
    width: 19px; height: 19px;
    background: var(--icon-orange);
    margin-right: 26px;
    flex: none;
    display: flex; align-items: center; justify-content: center;
  }

  .product-visual {
    position: absolute;
    background: linear-gradient(100deg, #55595d 0%, #3f4346 45%, #c96a2a 52%, #9a9da2 70%, #c3c5c9 100%);
    border-radius: 4px;
  }
  .card--front .product-visual { left: 633px; top: 300px; width: 249px; height: 196px; }
  .card--back .product-visual { left: 542px; top: 136px; width: 326px; height: 257px; }
</style>
</head>
<body>

<section class="card card--front">
  <div class="brand">
    <div class="brand__name">BRINTEL WORKS<span class="brand__suffix">PTY LTD</span></div>
    <div class="brand__tagline">Gas fitting &amp; Plumbing Specialists</div>
    <div class="brand__sectors">Domestic | Commercial | Industrial<span class="brand__since">Est Since 1988</span></div>
  </div>

  <div class="band-blue"></div>
  <div class="panel-dark"></div>

  <ul class="contact-list">
    <li><span class="contact-icon"><svg width="13" height="13" viewBox="0 0 24 24"><path fill="#fff" d="M6.6 10.8a15 15 0 0 0 6.6 6.6l2.2-2.2c.3-.3.7-.4 1-.2 1.1.4 2.3.6 3.6.6.6 0 1 .4 1 1V20c0 .6-.4 1-1 1A17 17 0 0 1 3 4c0-.6.4-1 1-1h3.5c.6 0 1 .4 1 1 0 1.3.2 2.5.6 3.6.1.3 0 .7-.2 1z"/></svg></span>07 3918 4726</li>
    <li><span class="contact-icon"><svg width="13" height="13" viewBox="0 0 24 24"><path fill="#fff" d="M6 2h12v5H6zM3 8h18a1 1 0 0 1 1 1v8h-4v5H6v-5H2V9a1 1 0 0 1 1-1zm5 8v4h8v-4z"/></svg></span>07 3918 4790</li>
    <li><span class="contact-icon"><svg width="13" height="13" viewBox="0 0 24 24"><circle cx="12" cy="12" r="9" fill="none" stroke="#fff" stroke-width="2.4"/><path d="M3 12h18M12 3c3 3 3 15 0 18M12 3c-3 3-3 15 0 18" fill="none" stroke="#fff" stroke-width="1.6"/></svg></span>www.brintelworks.com.au</li>
    <li><span class="contact-icon"><svg width="13" height="11" viewBox="0 0 24 18"><rect x="1" y="1" width="22" height="16" fill="none" stroke="#fff" stroke-width="2"/><path d="M1 1l11 9 11-9" fill="none" stroke="#fff" stroke-width="2"/></svg></span>admin@brintelworks.com.au</li>
    <li><span class="contact-icon"><svg width="11" height="14" viewBox="0 0 18 24"><path fill="#fff" d="M9 0a9 9 0 0 0-9 9c0 6.7 9 15 9 15s9-8.3 9-15a9 9 0 0 0-9-9zm0 12.5A3.5 3.5 0 1 1 9 5.5a3.5 3.5 0 0 1 0 7z"/></svg></span>PO Box 2204, Coorparoo, QLD 4151</li>
  </ul>

  <div class="product-visual" role="img" aria-label="Photo of a freestanding wood heater with glowing fire beside two hot water cylinders"></div>
</section>

<section class="card card--back">
  <div class="brand">
    <div class="brand__name">BRINTEL WORKS<span class="brand__suffix">PTY LTD</span></div>
    <div class="brand__tagline">Gas fitting &amp; Plumbing Specialists</div>
    <div class="brand__sectors">Domestic | Commercial | Industrial<span class="brand__since">Est Since 1988</span></div>
  </div>

  <div class="product-visual" role="img" aria-label="Photo of a freestanding wood heater with glowing fire beside two hot water cylinders"></div>
</section>

</body>
</html>
```